Quillmarsh Property Solutions need a business card design

Hello guys. We would need a business card design asap please.
We are a start up property investment business based in London UK specialised in buying, selling, managing and letting properties and helping distressed property owners.
The name of our Business is Quillmarsh, the logo symbolises the four fundamental elements of the world (earth, air, fire and water) and so it stands for strength, stability, longevity.
We would like the business card to communicate professionalism and reliability. Many many thanks indeed for your work.

Details:

1.) Rosalind Updike
Property Investor
Mobile: +44(0)7700123456
Email: rosalind.quillmarsh@mailbox-example.com

2.) Dominic Updike
Property Investor
Mobile: +44(0)7700987654
Email: dominic.quillmarsh@mailbox-example.com

```html
<!DOCTYPE html>
<html lang="en">
<head>
<meta charset="utf-8">
<title>Quillmarsh Property Solutions – Business Card</title>
<link href="https://fonts.googleapis.com/css2?family=Jost:wght@600&family=Open+Sans:wght@400;600&display=swap" rel="stylesheet">
<style>
  :root {
    --backdrop: #e4e4ea;
    --card: #ffffff;
    --ink: #111111;
    --name-red: #c8202f;
    --title-blue: #2f5fae;
    --icon-blue: #3d6cb5;
    --text-grey: #4a4a4a;
    --divider: #c4c4c4;
  }
  * { box-sizing: border-box; margin: 0; padding: 0; }
  html, body {
    width: 1200px; height: 987px; overflow: hidden;
    background: var(--backdrop);
  }
  .canvas {
    width: 1200px; height: 987px;
    display: flex; flex-direction: column;
    align-items: center; justify-content: center; gap: 40px;
  }
  .card {
    width: 740px; height: 423px;
    background: var(--card);
    border-radius: 28px;
    box-shadow: 0 6px 18px rgba(0,0,0,0.12);
    position: relative;
    overflow: hidden;
  }

  /* Back: brand face */
  .card--back {
    display: flex; flex-direction: column; justify-content: center;
    padding-left: 150px;
  }
  .brand {
    font-family: "Jost", sans-serif; font-weight: 600;
    color: var(--ink); text-transform: uppercase; line-height: 1;
  }
  .card--back .brand__name { font-size: 62px; letter-spacing: 2px; }
  .card--back .brand__tagline { font-size: 26px; letter-spacing: 2px; margin-top: 12px; }

  /* Front: contact face */
  .card--front { display: flex; align-items: center; }
  .front__brand {
    width: 310px; padding-left: 40px;
    display: flex; flex-direction: column; align-items: flex-start;
  }
  .brand__mark {
    width: 22px; height: 22px; background: var(--ink);
    margin-bottom: 16px;
  }
  .card--front .brand__name { font-size: 34px; letter-spacing: 1px; }
  .card--front .brand__tagline { font-size: 13px; letter-spacing: 1px; margin-top: 6px; }
  .front__divider {
    width: 1px; height: 190px; background: var(--divider);
  }
  .contact {
    padding-left: 30px;
    font-family: "Open Sans", sans-serif;
  }
  .contact__name { color: var(--name-red); font-weight: 600; font-size: 28px; line-height: 1.1; }
  .contact__role { color: var(--title-blue); font-size: 21px; margin-bottom: 22px; }
  .contact__line {
    display: flex; align-items: center; gap: 10px;
    color: var(--text-grey); font-size: 17px; margin-top: 10px;
  }
  .contact__icon { width: 18px; height: 18px; flex: none; fill: var(--icon-blue); }
</style>
</head>
<body>
<main class="canvas">

  <section class="card card--back" aria-label="Card back">
    <div class="brand">
      <div class="brand__name">Quillmarsh</div>
      <div class="brand__tagline">Property Solutions</div>
    </div>
  </section>

  <section class="card card--front" aria-label="Card front">
    <div class="front__brand brand">
      <span class="brand__mark" aria-hidden="true"></span>
      <div class="brand__name">Quillmarsh</div>
      <div class="brand__tagline">Property Solutions</div>
    </div>
    <div class="front__divider" aria-hidden="true"></div>
    <div class="contact">
      <div class="contact__name">Dominic Updike</div>
      <div class="contact__role">Property Investor</div>
      <div class="contact__line">
        <svg class="contact__icon" viewBox="0 0 18 18" aria-hidden="true">
          <rect x="4" y="1" width="10" height="16" rx="2"/>
          <rect x="6" y="3" width="6" height="6" fill="#fff"/>
          <circle cx="9" cy="13.5" r="1.3" fill="#fff"/>
        </svg>
        <span>+44(0)7700987654</span>
      </div>
      <div class="contact__line">
        <svg class="contact__icon" viewBox="0 0 18 18" aria-hidden="true">
          <rect x="1" y="4" width="16" height="11" rx="1.5"/>
          <path d="M2 5 L9 10.5 L16 5" fill="none" stroke="#fff" stroke-width="1.6"/>
        </svg>
        <span>dominic.quillmarsh@mailbox-example.com</span>
      </div>
    </div>
  </section>

</main>
</body>
</html>
```